Law Offices business card

Hi there, I'll need business card for the Law Offices of Colin Matheny. The information must convey his strategic approach and quick resolution to complex business litigation needs. Please emphasize Civil Litigation, Corporate Law, Business Governance and Real Estate Law. Colin has over 25 years of experience in these fields.The card should be modern and edgy and the message should be clear. Please consult his current website for ideas.

```html
<!DOCTYPE html>
<html lang="en">
<head>
<meta charset="utf-8">
<title>Law Offices of Colin Matheny – Business Card</title>
<link rel="stylesheet" href="https://fonts.googleapis.com/css2?family=Playfair+Display:wght@700&family=Arimo:wght@400;700&display=swap">
<style>
  :root {
    --stage: #3a3a3c;
    --card-red: #c44c4c;
    --card-black: #0b0b0b;
    --accent-red: #d0484b;
    --ink-light: #ffffff;
    --ink-soft: #d9d9d9;
    --ink-muted: #bdbdbd;
    --rule: #6a6a6a;
  }
  * { margin: 0; padding: 0; box-sizing: border-box; }
  html, body {
    width: 1200px; height: 950px; overflow: hidden;
    background: var(--stage);
    font-family: "Arimo", Arial, sans-serif;
  }
  .stage {
    width: 1200px; height: 950px;
    display: flex; flex-direction: column; align-items: center; justify-content: center;
    gap: 56px;
  }
  .card {
    position: relative;
    width: 700px; height: 400px;
    box-shadow: 0 14px 30px rgba(0,0,0,.35);
  }
  .card--front { background: var(--card-red); }
  .card--back { background: var(--card-black); }

  /* Firm name wordmark */
  .firm-name {
    font-family: "Playfair Display", Georgia, serif;
    font-weight: 700;
    color: var(--ink-light);
    display: flex; align-items: center; gap: 14px;
  }
  .firm-name__mark {
    width: 22px; height: 22px; background: var(--accent-red); flex: none;
  }
  .card--front .firm-name__mark { background: var(--ink-light); }
  .firm-name__text { line-height: 1.05; }
  .firm-name__kicker { display: block; font-size: 15px; letter-spacing: .06em; text-transform: uppercase; }
  .firm-name__title { display: block; font-size: 38px; }

  .card--front .firm-name {
    position: absolute; left: 50%; top: 128px; transform: translateX(-50%);
    white-space: nowrap;
  }
  .front-web {
    position: absolute; left: 0; right: 0; top: 262px;
    display: flex; align-items: center; justify-content: center; gap: 16px;
    color: var(--ink-light); font-size: 15px; letter-spacing: .28em;
  }
  .front-web::before, .front-web::after {
    content: ""; width: 70px; height: 1px; background: rgba(255,255,255,.8);
  }

  .card--back .firm-name {
    position: absolute; right: 48px; top: 70px; white-space: nowrap;
  }
  .contact {
    position: absolute; left: 56px; bottom: 46px; color: var(--ink-light);
  }
  .contact__name { color: var(--accent-red); font-size: 22px; }
  .contact__role { font-size: 16px; margin: 4px 0 14px; color: var(--ink-soft); }
  .contact__list { list-style: none; font-size: 16px; color: var(--ink-soft); }
  .contact__list li { display: flex; align-items: center; gap: 10px; height: 22px; }
  .contact__list svg { width: 14px; height: 14px; fill: var(--accent-red); flex: none; }

  .divider {
    position: absolute; left: 372px; bottom: 62px; width: 1px; height: 120px; background: var(--rule);
  }
  .office {
    position: absolute; left: 396px; bottom: 112px;
    font-style: normal; font-size: 16px; line-height: 24px; color: var(--ink-soft);
  }
  .office__web { letter-spacing: .16em; }
</style>
</head>
<body>
<main class="stage">
  <section class="card card--front" aria-label="Card front">
    <div class="firm-name">
      <span class="firm-name__mark"></span>
      <span class="firm-name__text">
        <span class="firm-name__kicker">Law Offices of</span>
        <span class="firm-name__title">Colin Matheny, PA</span>
      </span>
    </div>
    <p class="front-web">www.mathenylaw.com</p>
  </section>

  <section class="card card--back" aria-label="Card back">
    <div class="firm-name">
      <span class="firm-name__mark"></span>
      <span class="firm-name__text">
        <span class="firm-name__kicker">Law Offices of</span>
        <span class="firm-name__title">Colin Matheny, PA</span>
      </span>
    </div>

    <div class="contact">
      <p class="contact__name">Ellis Warner</p>
      <p class="contact__role">President</p>
      <ul class="contact__list">
        <li><svg viewBox="0 0 14 14" aria-hidden="true"><path d="M1 4c0-2 2-3 4-3l1 3-2 1c1 2 2 4 4 5l1-2 3 1c0 2-1 4-3 4C5 13 1 9 1 4z"/></svg>412 6190 3375</li>
        <li><svg viewBox="0 0 14 14" aria-hidden="true"><path d="M4 0h6a1 1 0 0 1 1 1v12a1 1 0 0 1-1 1H4a1 1 0 0 1-1-1V1a1 1 0 0 1 1-1zm1 2v8h4V2z"/></svg>730 2841 6092</li>
        <li><svg viewBox="0 0 14 14" aria-hidden="true"><path d="M3 1h7v4H3zM1 6h12v6H1zm2 2v1h2V8z"/></svg>915 3307 4418</li>
        <li><svg viewBox="0 0 14 14" aria-hidden="true"><path d="M1 3h12v8H1zm1 1 5 4 5-4v-.2H2z"/></svg>ellis@mathenylaw.com</li>
      </ul>
    </div>

    <span class="divider"></span>

    <address class="office">
      4120 Harbor Ridge Lane<br>
      Linden Bay, NY 11020<br>
      <span class="office__web">www.mathenylaw.com</span>
    </address>
  </section>
</main>
</body>
</html>
```